Thornvale Group needs a business card design

We need a new business card design using the logo recently selected in a logo competition on Pixel Bazaar. Our business is a consultancy specializing in aviation and energy and the winning business card design will promote an image of precision and professionalism with creativity.

Please use the logo with the name on the front of the card and use a complementary font. Make the back white with either the light grey or dark grey logo.

Target Market(s)

Senior finance and legal leaders at aviation and energy companies

Industry/Entity Type

Management Consulting

Contact Information for Business Card

Peter Castrell
President
Thornvale Group

www.thornvalegroup.example

(555) 204-6391
pc@thornvalegroup.example

Requirements
Must have
• Professional font that goes well with the logo font

```html
<!DOCTYPE html>
<html lang="en">
<head>
<meta charset="utf-8">
<title>Thornvale Group – Business Card</title>
<link href="https://fonts.googleapis.com/css2?family=Arimo:wght@400;700&display=swap" rel="stylesheet">
<style>
  :root {
    --navy: #123a6b;
    --navy-deep: #0b2a52;
    --navy-light: #1f4f86;
    --ink: #3c3f44;
    --rule: #1d3f6e;
    --paper: #ffffff;
    --paper-shade: #eef0f3;
    --backdrop: #d9dbde;
    --muted-white: #c9d3e0;
  }
  * { margin: 0; padding: 0; box-sizing: border-box; }
  html, body {
    width: 1200px; height: 950px; overflow: hidden;
    background: var(--backdrop);
    font-family: "Arimo", Arial, sans-serif;
  }
  .stage { position: relative; width: 1200px; height: 950px; }

  .card {
    position: absolute;
    width: 700px; height: 400px;
    box-shadow: 0 6px 18px rgba(0,0,0,0.18);
  }

  /* Reverse side */
  .card--back {
    left: 90px; top: 45px;
    background: linear-gradient(100deg, var(--navy-deep) 0%, var(--navy) 60%, var(--navy-light) 100%);
  }
  .card--back .back-name {
    position: absolute; left: 0; right: 0; top: 160px;
    text-align: center;
    color: var(--paper);
    font-size: 44px; font-weight: 400; letter-spacing: 6px;
    text-transform: uppercase;
  }
  .card--back .back-web {
    position: absolute; right: 40px; bottom: 34px;
    color: var(--muted-white);
    font-size: 17px; letter-spacing: 2px;
  }

  /* Front side */
  .card--front {
    left: 410px; top: 505px;
    background: linear-gradient(180deg, var(--paper) 55%, var(--paper-shade) 100%);
  }
  .brand {
    position: absolute; left: 44px; top: 70px;
    color: var(--navy);
    font-size: 34px; font-weight: 400; letter-spacing: 4px;
    text-transform: uppercase;
  }
  .divider {
    position: absolute; left: 44px; right: 60px; top: 178px;
    height: 2px; background: var(--rule);
  }
  .edge-tab {
    position: absolute; right: 0; top: 160px;
    width: 10px; height: 38px; background: var(--navy);
  }
  .holder {
    position: absolute; right: 60px; top: 118px; text-align: right;
  }
  .holder .name { color: var(--navy); font-size: 26px; font-weight: 700; }
  .holder .title { color: var(--ink); font-size: 20px; margin-top: 4px; }

  .contact {
    position: absolute; left: 44px; top: 214px;
    list-style: none;
    color: var(--ink); font-size: 19px; line-height: 29px;
  }
  .contact li { display: flex; align-items: center; gap: 10px; }
  .contact svg { width: 18px; height: 18px; fill: var(--navy); flex: none; }

  .company {
    position: absolute; right: 60px; top: 270px;
    text-align: right; color: var(--ink);
    font-size: 19px; line-height: 25px;
  }
</style>
</head>
<body>
<main class="stage">

  <section class="card card--back" aria-label="Card back">
    <p class="back-name">Thornvale Group</p>
    <p class="back-web">www.thornvalegroup.example</p>
  </section>

  <section class="card card--front" aria-label="Card front">
    <p class="brand">Thornvale Group</p>
    <div class="holder">
      <p class="name">Peter Castrell</p>
      <p class="title">President</p>
    </div>
    <div class="divider"></div>
    <div class="edge-tab"></div>

    <ul class="contact">
      <li>
        <svg viewBox="0 0 24 24" aria-hidden="true"><path d="M6.6 10.8a15.1 15.1 0 0 0 6.6 6.6l2.2-2.2c.3-.3.7-.4 1-.2 1.1.4 2.3.6 3.6.6.6 0 1 .4 1 1V20c0 .6-.4 1-1 1A17 17 0 0 1 3 4c0-.6.4-1 1-1h3.5c.6 0 1 .4 1 1 0 1.3.2 2.5.6 3.6.1.3 0 .7-.2 1z"/></svg>
        (555) 204-6391
      </li>
      <li>
        <svg viewBox="0 0 24 24" aria-hidden="true"><path d="M2 5h20v14H2z M2 5l10 8 10-8" /></svg>
        pc@thornvalegroup.example
      </li>
      <li>
        <svg viewBox="0 0 24 24" aria-hidden="true"><circle cx="12" cy="12" r="10"/></svg>
        www.thornvalegroup.example
      </li>
    </ul>

    <div class="company">
      <p>Thornvale Group LLC</p>
      <p>Finance and Strategy Consulting</p>
      <p>Aviation - Manufacturing - Energy</p>
    </div>
  </section>

</main>
</body>
</html>
```